Contemporary Business card for Event Manager

Needed for my startup events company in Melbourne. Events I manage will be based within the fashion industry, sporting events, product launches etc. Not weddings or small dinner parties. Therfore I am after something professional and aimed at high end corporate market; but with the added emphasis on not being too conservative or boring. I am happy with a pop of colour e.g. yellow or copper foil.

Target Market(s)

fashion industry, design industry, high end sporting events e.g. Polo, Grand Prix, corporate clients,

Industry/Entity Type

Fashion

Contact Information for Business Card

side 1
Lucy Brandt (can be upper or lower case, have a feature full stop between first and surname, or at the end of the nameetc) I am open to ideas. I would also be fine with my initials or name as a logo on the front (if this is the case my full name would need to go on the second side of the card.
2nd side:
Mobile: +61 400 817 263
email: lucy.brandt@mailnest.com.au

on one side of the card:
event management | brand activation | Advisory Services

Font styles to use
Serif
Sans Serif

Requirements
Must have
• side 2 must have
• mobile number
• email address
• event management | brand activation | Advisory Services
• ** my full name (Lucy Brandt) must be on the card somewhere)
Nice to have
• 1st side
• I see the card stock being either a dark grey, light grey, natural white or black (all matt colours on unprocessed card). I see the writing being copper foil, or foil white or foil black.
• To give you a feel for me, think: contemporary, minimalist, I love line drawings, concrete, white with grey vein marble, copper, white, grey, black...yes I do like colour....yellow (but pops of colour) ;) I would like the card to look designer but 'on trend' as I deal with a lot of design and fashion clients....styles - think the sophistication and simplicity of Vireaux or urban contemporary.
• some examples of what I like. Although please don't leet this limit you...I really am happy to have something a little more urban or design focused like a line drawing of an object, person too or a photo image too.
• https://www.moodtackle.com/pin/830165427719302846/
• https://www.moodtackle.com/pin/607281935540173268/
• https://www.moodtackle.com/pin/318746205913457092/
• https://www.moodtackle.com/pin/41983627530918476/
• https://www.moodtackle.com/pin/53128940672419087/
• https://www.moodtackle.com/pin/90316284750638152/
• https://www.moodtackle.com/pin/734092618450362918/
• https://www.moodtackle.com/pin/926354081736215407/
• https://www.moodtackle.com/pin/481627093518704356/
Should not have
• should not look commercial or have cartoonish looking logos. However happy with a simple line drawing or logo with initials etc.

```html
<!DOCTYPE html>
<html lang="en">
<head>
<meta charset="utf-8">
<title>Lucy Brandt — Business Card</title>
<link rel="stylesheet" href="https://fonts.googleapis.com/css2?family=Questrial&display=swap">
<style>
  :root {
    --backdrop: #e4e0da;
    --card-black: #0c0c0d;
    --card-white: #ffffff;
    --red: #e0002a;
    --blush: #f5b8c2;
    --ink: #2a2a2a;
    --light-ink: #e8e8e8;
  }
  html, body {
    margin: 0;
    padding: 0;
    width: 1200px;
    height: 892px;
    overflow: hidden;
    background: var(--backdrop);
    font-family: "Questrial", sans-serif;
  }
  .card {
    position: absolute;
    left: 250px;
    width: 700px;
    height: 400px;
    border-radius: 26px;
    overflow: hidden;
    box-shadow: 0 10px 28px rgba(0,0,0,0.22);
  }
  .card svg { position: absolute; inset: 0; display: block; }
  .card-front { top: 30px; background: var(--card-black); }
  .card-back { top: 462px; background: var(--card-white); }

  .name {
    position: absolute;
    right: 60px;
    top: 170px;
    margin: 0;
    text-align: right;
    color: var(--red);
    font-weight: 400;
    line-height: 1;
  }
  .name-first {
    display: block;
    font-size: 92px;
    letter-spacing: 2px;
  }
  .name-last {
    display: block;
    margin-top: 8px;
    font-size: 50px;
    letter-spacing: 14px;
    margin-right: -14px;
  }

  .services {
    position: absolute;
    left: 430px;
    top: 34px;
    margin: 0;
    padding: 0;
    list-style: none;
    color: var(--ink);
    font-size: 19px;
    line-height: 1.3;
    letter-spacing: 1px;
  }
  .contact {
    position: absolute;
    left: 40px;
    bottom: 34px;
    font-style: normal;
    font-size: 24px;
    letter-spacing: 1.5px;
    line-height: 1.4;
    color: var(--light-ink);
  }
  .contact-email .user { color: var(--red); }
</style>
</head>
<body>

<section class="card card-front" aria-label="Card front">
  <svg viewBox="0 0 700 400" width="700" height="400" aria-hidden="true">
    <rect class="accent-bar" x="0" y="0" width="18" height="400" fill="var(--red)"/>
    <line class="rule" x1="60" y1="60" x2="260" y2="60" stroke="var(--blush)" stroke-width="1.5"/>
    <rect class="accent-dot" x="60" y="80" width="14" height="14" fill="var(--red)"/>
    <line class="name-rule" x1="400" y1="356" x2="640" y2="356" stroke="var(--red)" stroke-width="2"/>
  </svg>
  <h1 class="name">
    <span class="name-first">Lucy</span>
    <span class="name-last">Brandt</span>
  </h1>
</section>

<section class="card card-back" aria-label="Card back">
  <svg viewBox="0 0 700 400" width="700" height="400" aria-hidden="true">
    <polygon class="dark-field" points="0,230 700,150 700,400 0,400" fill="var(--card-black)"/>
    <line class="edge-rule" x1="0" y1="218" x2="700" y2="138" stroke="var(--red)" stroke-width="3"/>
    <rect class="accent-dot" x="400" y="40" width="12" height="12" fill="var(--red)"/>
  </svg>
  <ul class="services">
    <li>event management</li>
    <li>brand activation</li>
    <li>Advisory Services</li>
  </ul>
  <address class="contact">
    <div class="contact-phone">+61 400 817 263</div>
    <div class="contact-email"><span class="user">lucy.brandt</span>@mailnest.com.au</div>
  </address>
</section>

</body>
</html>
```